New Mechanical Maintenance business needs website

New Mechanical Maintenance business in Perth Western Australia needs a nice and easy to navigate website. Showing what we do and how we can be the right fit for other small to medium size business by offering personalized service from our highly skilled team. We deal with both fixed plant repairs like food and chemical processing facilities to heavy equipment like drill rigs, Large boats and earthmoving equipment.

Target Market(s)

Small to medium business to offer personalized services/packages

Industry/Entity Type

e deal with both fixed plant repairs like food and chemical processing facilities to heavy equipment like drill rigs, Large boats and earthmoving equipment.

Coding

Coded - Design and coding required

Number of Pages Required

4 page

Font styles to use
Serif

Colors
0054AA
0677BA
7BADD7
CADEEF
E8F1F8

Requirements
Must have
• A website that is easy to navigate but covers off on the range of services/maintenance we can provide

```html
<!DOCTYPE html>
<html lang="en">
<head>
<meta charset="utf-8">
<title>Ridgeway Maintenance</title>
<link href="https://fonts.googleapis.com/css2?family=Roboto:ital,wght@0,400;0,500;0,700;1,500;1,700&display=swap" rel="stylesheet">
<style>
:root{
  --navy:#0054AA;
  --blue:#0677BA;
  --sky:#7BADD7;
  --mist:#CADEEF;
  --ice:#E8F1F8;
  --ink:#333;
  --text:#555;
  --heading:#4a4f55;
  --footer:#5a5c5f;
  --white:#fff;
}
*{box-sizing:border-box;margin:0;padding:0}
html,body{width:1200px;height:4323px;overflow:hidden}
body{font-family:"Roboto",Arial,sans-serif;color:var(--text);background:var(--white);position:relative}
.section{position:absolute;left:0;width:1200px}
.heading{font-style:italic;font-weight:700;font-size:38px;color:var(--heading);text-align:center;letter-spacing:-1px}
.heading::after{content:"";display:block;width:56px;height:3px;background:var(--blue);margin:8px auto 0}
.btn{display:inline-block;background:var(--blue);color:var(--white);font-weight:700;font-size:14px;border-radius:26px;padding:0 26px;height:50px;line-height:50px;text-transform:uppercase}
.btn-soft{display:inline-block;background:var(--ice);color:var(--blue);font-weight:700;font-size:14px;border-radius:24px;padding:0 24px;height:46px;line-height:46px;text-transform:uppercase}

/* header */
.site-header{top:0;height:136px;background:var(--white)}
.brand{position:absolute;left:111px;top:20px;display:flex;align-items:center;gap:12px}
.brand-mark{width:50px;height:50px;border-radius:50%;background:var(--footer)}
.brand-name{font-weight:700;font-size:22px;color:var(--footer);letter-spacing:2px}
.nav{position:absolute;left:370px;top:64px;display:flex;gap:36px;font-weight:700;font-size:13px;color:#444}
.nav .active{color:var(--blue)}
.nav-cta{position:absolute;left:818px;top:52px;background:var(--blue);color:#fff;font-weight:700;font-size:12px;border-radius:22px;width:134px;height:42px;line-height:42px;text-align:center}
.socials{position:absolute;left:982px;top:59px;display:flex;gap:9px}
.socials span{width:28px;height:28px;border-radius:50%;background:#fff;box-shadow:0 2px 8px rgba(0,0,0,.18)}

/* hero */
.hero{top:136px;height:644px;background:linear-gradient(100deg,#3a3026 0%,#8c5a22 30%,#4a4f58 60%,#1f2733 100%)}
.hero-card{position:absolute;left:111px;top:171px;width:577px;height:303px;background:rgba(255,255,255,.82);padding:34px 33px}
.hero-kicker{font-style:italic;font-weight:500;font-size:21px;color:var(--blue)}
.hero-title{font-style:italic;font-weight:700;font-size:42px;color:var(--heading);letter-spacing:-1px;margin-top:2px}
.hero-text{font-size:19px;line-height:31px;color:#222;margin:18px 0 22px}
.dots{position:absolute;left:562px;top:598px;display:flex;gap:16px;align-items:center}
.dots i{width:6px;height:6px;border-radius:50%;background:#fff}
.dots i.on{width:22px;height:22px;border:2px solid #fff;background:transparent;position:relative}
.dots i.on::after{content:"";position:absolute;left:5px;top:5px;width:8px;height:8px;border-radius:50%;background:#fff}

/* who */
.who{top:780px;height:574px;text-align:center}
.who .heading{margin-top:114px}
.who p{width:960px;margin:36px auto 0;font-size:15px;line-height:28.5px}
.who p+p{margin-top:14px}
.who .btn{margin-top:34px;height:50px}

/* what */
.what{top:1354px;height:682px;background:var(--ice)}
.what .heading{margin-top:82px}
.service{position:absolute;top:180px;width:305px;height:412px;background:#fff;box-shadow:0 3px 12px rgba(0,0,0,.12);text-align:center;padding-top:33px}
.service.featured{background:var(--blue);color:#fff}
.service-icon{width:94px;height:94px;border-radius:50%;background:var(--blue);margin:0 auto;display:flex;align-items:center;justify-content:center}
.service.featured .service-icon{background:#fff}
.service h3{font-size:18px;font-weight:700;color:#333;margin:26px 0 18px}
.service.featured h3{color:#fff}
.service p{font-size:14px;line-height:26px;padding:0 26px;margin-bottom:24px}
.service.featured .btn-soft{background:#fff}
.arrow{position:absolute;width:34px;height:34px;border-radius:50%;display:flex;align-items:center;justify-content:center}

/* why */
.why{top:2036px;height:657px}
.why-frame{position:absolute;left:111px;top:128px;width:470px;height:411px;border:2px solid var(--blue)}
.why-photo{position:absolute;left:128px;top:110px;width:472px;height:411px;background:linear-gradient(180deg,#9fc0d9 0%,#cdd6d6 35%,#6b7a7d 60%,#3d4649 100%)}
.why-rule{position:absolute;left:560px;top:161px;width:94px;height:2px;background:var(--blue)}
.why-copy{position:absolute;left:673px;top:140px;width:416px}
.why-copy h2{font-style:italic;font-weight:700;font-size:36px;color:var(--heading);letter-spacing:-1px}
.why-copy p{font-size:15px;line-height:28.5px;text-align:justify;margin-top:14px}
.why-copy p:first-of-type{margin-top:22px}
.why-copy .btn{margin-top:30px}

/* industries */
.industries{top:2693px;height:641px;background:linear-gradient(180deg,#0f5f9e 0%,var(--blue) 40%,var(--blue) 100%)}
.industries .heading{color:#fff;margin-top:58px}
.industries .heading::after{background:#fff}
.industry{position:absolute;top:152px;width:305px;height:422px;background:#fff;text-align:center;padding:6px 6px 0}
.industry-photo{height:210px}
.industry h3{font-size:18px;font-weight:500;color:#444;margin:26px 0 12px}
.industry p{font-size:14px;line-height:26px;padding:0 20px;margin-bottom:14px}
.industry .btn-soft{font-size:13px;height:38px;line-height:38px;padding:0 24px}

/* contact */
.contact{top:3334px;height:586px}
.contact .heading{margin-top:95px}
.info{position:absolute;top:186px;display:flex;gap:18px}
.info-icon{width:64px;height:64px;border-radius:50%;background:#fff;box-shadow:0 3px 10px rgba(0,0,0,.15);display:flex;align-items:center;justify-content:center;flex:none}
.info h4{font-size:14px;font-weight:700;color:#444;margin-top:8px}
.info p{font-size:14px;line-height:21px;margin-top:6px}
.field{position:absolute;background:#fff;box-shadow:0 2px 8px rgba(0,0,0,.14);font-size:14px;color:#555;padding:16px 17px}
.contact .btn{position:absolute;left:519px;top:451px;width:162px;text-align:center;padding:0}

/* footer */
.footer{top:3920px;height:403px;background:var(--footer);color:#fff}
.foot-brand{position:absolute;left:111px;top:100px;display:flex;align-items:center;gap:14px}
.foot-brand .brand-mark{width:62px;height:62px;background:#fff}
.foot-brand .brand-name{color:#fff;font-size:24px}
.foot-col{position:absolute;top:62px}
.foot-col h4{font-size:17px;font-weight:700;margin-bottom:16px}
.foot-col li{list-style:none;font-size:14px;line-height:50px;padding-left:30px;position:relative}
.foot-col li::before{content:"";position:absolute;left:0;top:23px;width:4px;height:4px;border-radius:50%;background:#fff}
.foot-contact p{font-size:14px;line-height:21px;padding-left:29px;position:relative;margin-bottom:10px}
.foot-contact svg{position:absolute;left:0;top:3px}
.foot-rule{position:absolute;left:111px;top:342px;width:978px;height:1px;background:rgba(255,255,255,.25)}
.foot-copy{position:absolute;left:0;width:1200px;top:370px;text-align:center;font-size:14px}
.foot-social{position:absolute;left:985px;top:361px;display:flex;gap:10px}
.foot-social span{width:28px;height:28px;border-radius:50%;background:#fff}
.foot-social span:first-child{background:var(--blue)}
</style>
</head>
<body>

<header class="section site-header">
  <div class="brand"><span class="brand-mark"></span><span class="brand-name">RIDGEWAY</span></div>
  <nav class="nav">
    <span class="active">HOME</span><span>WHO WE ARE</span><span>WHAT WE DO</span><span>RESOURCES</span>
  </nav>
  <div class="nav-cta">CONTACT US</div>
  <div class="socials" aria-label="Social links"><span></span><span></span><span></span></div>
</header>

<section class="section hero" role="img" aria-label="Two engineers in hard hats looking across a busy industrial plant floor">
  <div class="hero-card">
    <div class="hero-kicker">WELCOME TO</div>
    <div class="hero-title">RIDGEWAY MAINTENANCE</div>
    <p class="hero-text">Lorem ipsum dolor sit amet, consectetur adipiscing elit,<br>sed do eiusmod tempor incidea.</p>
    <span class="btn">GET STARTED</span>
  </div>
  <div class="dots"><i></i><i class="on"></i><i></i><i></i></div>
</section>

<section class="section who">
  <h2 class="heading">WHO WE ARE</h2>
  <p>Director of the company has over 20-year experience in the fixed and mobile plant industries ranging from Perth local and overseas. Facilities like precious metals refining, offshore drilling and production platform, open cut and underground mining, civils, geotechnical and construction equipment and large-scale construction as an expat overseas.</p>
  <p>Lorem ipsum dolor sit amet, consectetur adipiscing elit, sed do eiusmod tempor incididunt ut labore et dolore magna aliqua. Ut enim ad minim veniam, quis nostrud exercitation ullamco laboris nisi ut aliquip ex ea commodo consequat. Duis aute irure dolor in reprehenderit in voluptate velit esse cillum dolore eu fugiat nulla pariatur.</p>
  <span class="btn">LEARN MORE</span>
</section>

<section class="section what">
  <h2 class="heading">WHAT WE DO</h2>
  <div class="arrow" style="left:34px;top:372px;background:var(--mist)"><svg width="12" height="12" viewBox="0 0 12 12"><path d="M8 1 3 6l5 5" stroke="#555" stroke-width="2" fill="none"/></svg></div>
  <div class="arrow" style="left:1132px;top:372px;background:var(--blue)"><svg width="12" height="12" viewBox="0 0 12 12"><path d="M4 1l5 5-5 5" stroke="#fff" stroke-width="2" fill="none"/></svg></div>

  <article class="service" style="left:111px">
    <div class="service-icon"><svg width="46" height="46" viewBox="0 0 46 46" fill="none" stroke="#fff" stroke-width="2"><circle cx="23" cy="23" r="14"/><circle cx="23" cy="23" r="6"/><path d="M23 3v6M23 37v6M3 23h6M37 23h6"/></svg></div>
    <h3>FOOD PROCESSING</h3>
    <p>Lorem ipsum dolor sit amet, consectet adipiscing elit, sed do eiusmod tempor incididunt ut labore et dolore magna aliqua ut enim adea.</p>
    <span class="btn-soft">READ MORE</span>
  </article>
  <article class="service featured" style="left:447px">
    <div class="service-icon"><svg width="46" height="46" viewBox="0 0 46 46" fill="none" stroke="#555" stroke-width="2"><path d="M18 6h10M20 6v12l-9 18h24l-9-18V6"/><circle cx="23" cy="29" r="3"/></svg></div>
    <h3>CHEMICAL PROCESSING</h3>
    <p>Lorem ipsum dolor sit amet, consectet adipiscing elit, sed do eiusmod tempor incididunt ut labore et dolore magna aliqua ut enim adea.</p>
    <span class="btn-soft">READ MORE</span>
  </article>
  <article class="service" style="left:783px">
    <div class="service-icon"><svg width="46" height="46" viewBox="0 0 46 46" fill="none" stroke="#fff" stroke-width="2"><path d="M30 4v30M26 10h8M6 24h20v10H6z"/><circle cx="11" cy="38" r="3"/><circle cx="21" cy="38" r="3"/></svg></div>
    <h3>DRILL RIGS</h3>
    <p>Lorem ipsum dolor sit amet, consectet adipiscing elit, sed do eiusmod tempor incididunt ut labore et dolore magna aliqua ut enim adea.</p>
    <span class="btn-soft">READ MORE</span>
  </article>
</section>

<section class="section why">
  <div class="why-frame"></div>
  <div class="why-photo" role="img" aria-label="Refinery with tall columns and pipework under a blue sky"></div>
  <div class="why-rule"></div>
  <div class="why-copy">
    <h2>WHY WORK WITH US</h2>
    <p>Lorem ipsum dolor sit amet, consectetur adipiscing elit, sed do eiusmod tempor incididunt ut labore et dolore magna aliqua. Ut enim ad minim veniam, quis nostrud exercitation ullamco laboris nisi utea.</p>
    <p>Lorem ipsum dolor sit amet, consectetur adipiscing elit, sed do eiusmod tempor incididunt ut labore et dolore magna aliqua utenim ad minimea.</p>
    <span class="btn">LEARN MORE</span>
  </div>
</section>

<section class="section industries">
  <h2 class="heading">OUR INDUSTRIES</h2>
  <div class="arrow" style="left:34px;top:348px;background:#fff"><svg width="12" height="12" viewBox="0 0 12 12"><path d="M8 1 3 6l5 5" stroke="#333" stroke-width="2" fill="none"/></svg></div>
  <div class="arrow" style="left:1132px;top:348px;background:#fff"><svg width="12" height="12" viewBox="0 0 12 12"><path d="M4 1l5 5-5 5" stroke="#333" stroke-width="2" fill="none"/></svg></div>

  <article class="industry" style="left:111px">
    <div class="industry-photo" role="img" aria-label="Welder at work with sparks flying" style="background:linear-gradient(135deg,#3b3f44,#b0683a 55%,#e8c89a)"></div>
    <h3>LOREM IPSUM DOLOR</h3>
    <p>Lorem ipsum dolor sit amet, consectet adipiscing elit, sed do eiusmod tempor incididunt ut laborea.</p>
    <span class="btn-soft">READ MORE</span>
  </article>
  <article class="industry" style="left:447px">
    <div class="industry-photo" role="img" aria-label="Technician with tablet inspecting red pipe valves" style="background:linear-gradient(135deg,#6d7a88,#9a3a32 50%,#aab3ba)"></div>
    <h3>LOREM IPSUM DOLOR</h3>
    <p>Lorem ipsum dolor sit amet, consectet adipiscing elit, sed do eiusmod tempor incididunt ut laborea.</p>
    <span class="btn-soft">READ MORE</span>
  </article>
  <article class="industry" style="left:783px">
    <div class="industry-photo" role="img" aria-label="Earthmoving equipment in an open pit at sunset" style="background:linear-gradient(180deg,#5e6a7c,#d9874a 45%,#6b5b48)"></div>
    <h3>LOREM IPSUM DOLOR</h3>
    <p>Lorem ipsum dolor sit amet, consectet adipiscing elit, sed do eiusmod tempor incididunt ut laborea.</p>
    <span class="btn-soft">READ MORE</span>
  </article>
</section>

<section class="section contact">
  <h2 class="heading">CONTACT US</h2>
  <div class="info" style="left:186px">
    <div class="info-icon"><svg width="26" height="26" viewBox="0 0 26 26" fill="none" stroke="#0677BA" stroke-width="2"><path d="M13 23s-7-7-7-12a7 7 0 0 1 14 0c0 5-7 12-7 12z"/><circle cx="13" cy="11" r="2.5"/></svg></div>
    <div><h4>LOCATION:</h4><p>465, Lorum Ipsum Dolore Sed,<br>United States</p></div>
  </div>
  <div class="info" style="left:500px">
    <div class="info-icon"><svg width="26" height="26" viewBox="0 0 26 26" fill="none" stroke="#0677BA" stroke-width="2"><path d="M6 3l4 1 1 5-3 2a12 12 0 0 0 6 6l2-3 5 1 1 4c-1 2-3 3-5 3A17 17 0 0 1 3 8c0-2 1-4 3-5z"/></svg></div>
    <div><h4>CALL US:</h4><p>+1 (888) 888 8888</p></div>
  </div>
  <div class="info" style="left:735px">
    <div class="info-icon"><svg width="26" height="26" viewBox="0 0 26 26" fill="none" stroke="#0677BA" stroke-width="2"><rect x="3" y="6" width="20" height="14"/><path d="M3 6l10 8 10-8"/></svg></div>
    <div><h4>EMAIL US:</h4><p>info@ridgewaymaint.com</p></div>
  </div>
  <div class="field" style="left:166px;top:275px;width:283px;height:51px">Full Name</div>
  <div class="field" style="left:458px;top:275px;width:283px;height:51px">Phone</div>
  <div class="field" style="left:751px;top:275px;width:283px;height:51px">Email Address</div>
  <div class="field" style="left:166px;top:340px;width:868px;height:94px">Message</div>
  <span class="btn">SEND MESSAGE</span>
</section>

<footer class="section footer">
  <div class="foot-brand"><span class="brand-mark"></span><span class="brand-name">RIDGEWAY</span></div>
  <div class="foot-col" style="left:407px">
    <h4>NAVIGATION</h4>
    <ul><li>Home</li><li>Who We Are</li><li>What We Do</li><li>Resources</li><li>Contact Us</li></ul>
  </div>
  <div class="foot-col" style="left:609px">
    <h4>QUICK LINKS</h4>
    <ul><li>Privacy Policy</li><li>Terms &amp; Conditions</li><li>Legal Support</li><li>Disclaimer</li></ul>
  </div>
  <div class="foot-col foot-contact" style="left:840px">
    <h4>CONTACT US</h4>
    <p><svg width="14" height="14" viewBox="0 0 14 14"><path d="M7 13S2 8 2 5a5 5 0 0 1 10 0c0 3-5 8-5 8z" fill="#fff"/></svg>465, Lorum Ipsum Dolore Sed,<br>United States</p>
    <p><svg width="14" height="14" viewBox="0 0 14 14"><path d="M3 1l3 1v3L4 6a7 7 0 0 0 4 4l1-2h3l1 3c-1 2-2 2-3 2A11 11 0 0 1 1 4c0-2 1-3 2-3z" fill="#fff"/></svg>+1 (888) 888 8888</p>
    <p><svg width="14" height="14" viewBox="0 0 14 14"><rect x="1" y="3" width="12" height="9" fill="#fff"/><path d="M1 3l6 5 6-5" stroke="#5a5c5f" fill="none"/></svg>info@ridgewaymaint.com</p>
  </div>
  <div class="foot-rule"></div>
  <div class="foot-copy">© 2024 Ridgeway Maintenance &nbsp;|&nbsp; All Rights Reserved</div>
  <div class="foot-social" aria-label="Social links"><span></span><span></span><span></span></div>
</footer>

</body>
</html>
```